Zing Webcomic

A simple signup landing page and blog design for an upcoming webcomic. I am mostly looking for a flat UI with a simple color scheme. I want to showcase a large background image and the comic title image. I have all the technicals figured out (I am a web developer by trade), so all I need now is a solid design I like.

The signup for should only have one field (email) and have text above it, and smaller text below it.

The blog, I am thinking, should be in the style of comic book pages. The home page would be blocks with large white outlines, with the article pages being an extension of that. As I stated before, should be fairly minimalist, but fun. Also, no sidebar or ads, IE single column. I have attached a simple mockup/layout of the blog to give a general idea of what I am going for.

I have attached the Logo and Background art (uncolored) for reference. Don't worry about the background image blending in, I can take care of that when the design is implemented. I will be focusing on layout and overall look, not necessarily readability (which I can fix).

~Please DO NOT take these examples literally. I will describe what I like about each example.~

Signup pages:
http://example-plaza.test/landing-page-type-photo/
http://www.lanternhop.test/showcase/website-design/814/10-most-beautiful-landing-pages-in-minimalist-style
http://quillnest.test/47-modern-landing-pages-showcasing-inspirational-web-design/
Great examples of minimalist design. However, instead of text or other content, there should be a simple signup form, as described above. Also think a lot more "playful" rather than super professional.

Blog:
http://vrakk.test/
Awesome example of a single column, minimal design. Needs to be more "comicbook style" though.
http://tidyrows.test/
Another good example of minimal design blog.
http://makerbarn.test/wp-content/uploads/res-blogs-5.jpg
I like the timeline feel here. Combine that with a comic book page kind of thing, and I think you have a winner.

Actual webcomic landing (not required):
http://www.lunarfoxpanels.test/comic.php?date=20021104#.U90ysYBdUvU
I like the navigation. It makes the atmosphere nice for the comic. The page layout itself is WAY too busy.
http://www.dime-galaxy.test/comic/
Fairly common webcomic, but their navigation and page layout is nice.
http://qvmp.test/936/
Another common webcomic. The simple page layout makes it easy for people to get started I think.

So there you have it. I will try my best to keep updating and adding to the description. If you have any questions, please don't hesitate to ask.
Updates

Hey Guys, I am really appreciating all the effort you have been putting in. I am amazed to see all the awesome designs and all the care taken with the project. I am just writing everyone to let you know that I have uploaded a simple layout/wireframe of the blog, to give an idea of what I am going for. Can't wait to see how things progress, and good luck to everyone!

Industry/Entity Type

Trade

Font styles to use
Sans Serif

Requirements
Must have
• Must showcase a large background image (does not have to cover the entire background). Should be a flat UI as well. Should be mostly neutral with splashes of blue or purple. Social links should also be somewhere (twitter, facebook, etc.).
Nice to have
• I am thinking something with rounded boxes, but I can live without them. A more "fun" design as opposed to more professional is definitely nice to have.

If you would like to try a stab at the actual comic page display and navigation, you are welcome to submit something. It should not be a main priority though.

Being responsive is not a requirement, but it would be nice to have.
Should not have
• A billion links in the navigation or look too busy.
No sidebar or advertisements. Should be a clean design.

```html
<!DOCTYPE html>
<html lang="en">
<head>
<meta charset="utf-8">
<title>Zing Webcomic – Sign up</title>
<link rel="stylesheet" href="https://fonts.googleapis.com/css2?family=Kaushan+Script&family=Raleway:wght@700&family=Source+Sans+Pro:wght@400;600;700&display=swap">
<style>
  :root {
    --page-bg: #000000;
    --paper: #ffffff;
    --art-tone: #e4e4e4;
    --ink: #111111;
    --body-text: #333333;
    --muted-text: #8a8a8a;
    --field-border: #9a9a9a;
    --button-bg: #000000;
    --badge-orange: #f2a20c;
    --badge-yellow: #fbc226;
    --glow-purple: #5b3fa0;
    --icon-active: #f5b311;
  }
  html, body {
    margin: 0;
    padding: 0;
    width: 1200px;
    height: 676px;
    overflow: hidden;
    background: var(--page-bg);
  }
  .canvas {
    position: relative;
    width: 1200px;
    height: 676px;
    font-family: "Source Sans Pro", Arial, sans-serif;
  }
  .paper {
    position: absolute;
    left: 0;
    top: 0;
    width: 1200px;
    height: 676px;
    filter: drop-shadow(0 5px 4px var(--glow-purple));
  }
  .brand-name {
    position: absolute;
    top: 62px;
    left: 0;
    width: 1200px;
    text-align: center;
    font-weight: 700;
    font-size: 50px;
    letter-spacing: 4px;
    color: var(--ink);
    margin: 0;
    line-height: 1;
  }
  .headline {
    position: absolute;
    top: 158px;
    left: 396px;
    width: 408px;
    margin: 0;
    text-align: center;
    font-family: "Kaushan Script", cursive;
    font-weight: 400;
    font-size: 38px;
    line-height: 1;
    color: var(--ink);
    white-space: nowrap;
  }
  .tagline {
    position: absolute;
    top: 198px;
    right: 396px;
    margin: 0;
    font-size: 12px;
    color: var(--body-text);
    white-space: nowrap;
  }
  .intro {
    position: absolute;
    top: 242px;
    left: 0;
    width: 1200px;
    margin: 0;
    text-align: center;
    text-transform: uppercase;
    font-weight: 600;
    font-size: 15px;
    line-height: 23px;
    color: var(--body-text);
  }
  .signup-form {
    position: absolute;
    top: 301px;
    left: 439px;
    width: 322px;
  }
  .email-field {
    display: block;
    box-sizing: border-box;
    width: 322px;
    height: 42px;
    border: 1px solid var(--field-border);
    border-radius: 3px;
    background: var(--paper);
    text-align: center;
    font-family: "Source Sans Pro", Arial, sans-serif;
    font-size: 14px;
    color: var(--ink);
  }
  .email-field::placeholder { color: var(--muted-text); }
  .signup-button {
    display: block;
    width: 322px;
    height: 43px;
    margin-top: 24px;
    border: 0;
    border-radius: 3px;
    background: var(--button-bg);
    color: var(--paper);
    font-family: "Raleway", Arial, sans-serif;
    font-weight: 700;
    font-size: 15px;
    letter-spacing: 0.5px;
    text-transform: uppercase;
  }
  .fine-print {
    position: absolute;
    top: 430px;
    left: 436px;
    width: 328px;
    margin: 0;
    text-align: center;
    font-size: 12.5px;
    line-height: 19px;
    color: var(--muted-text);
  }
  .blog-badge {
    position: absolute;
    left: 798px;
    top: 456px;
    width: 120px;
    height: 120px;
  }
  .blog-badge-label {
    position: absolute;
    left: 0;
    top: 0;
    width: 120px;
    height: 120px;
    display: flex;
    flex-direction: column;
    align-items: center;
    justify-content: center;
    color: var(--paper);
    text-decoration: none;
    text-transform: uppercase;
    font-weight: 700;
    line-height: 1;
  }
  .blog-badge-label .small { font-size: 14px; font-weight: 600; }
  .blog-badge-label .large { font-size: 22px; margin-top: 2px; }
  .social-links {
    position: absolute;
    top: 612px;
    left: 0;
    width: 1200px;
    display: flex;
    justify-content: center;
    gap: 9px;
    margin: 0;
    padding: 0;
    list-style: none;
  }
  .social-links a {
    display: block;
    width: 24px;
    height: 24px;
    border-radius: 50%;
    background: var(--paper);
  }
  .social-links a.is-active { background: var(--icon-active); }
  .copyright {
    position: absolute;
    top: 648px;
    left: 0;
    width: 1200px;
    margin: 0;
    text-align: center;
    font-size: 11px;
    color: var(--paper);
  }
</style>
</head>
<body>
<main class="canvas">
  <svg class="paper" viewBox="0 0 1200 676" aria-hidden="true">
    <defs>
      <clipPath id="paper-edge">
        <path id="paper-shape" d="M330,60 L344,56 352,52 360,58 372,50 384,46 397,52 410,50 421,42 432,38 445,46 455,44 462,34 470,30 486,32 500,28 511,25 520,22 534,28 548,26 562,20 575,18 588,24 600,22 615,16 630,18 645,25 660,24 676,18 690,20 700,27 712,28 726,26 740,30 754,36 768,38 780,32 790,34 801,42 812,44 826,38 840,40 853,44 866,46 870,58 874,70 868,86 870,100 876,120 878,140 870,165 872,190 878,214 880,240 872,270 874,300 880,330 882,360 874,392 876,420 882,446 880,470 874,492 872,510 866,528 860,540 846,544 830,548 815,553 800,556 786,550 770,552 755,558 740,560 720,554 700,556 680,562 660,562 640,556 620,556 600,563 580,562 560,555 540,556 520,561 500,560 480,552 460,552 440,558 420,556 404,548 390,548 374,554 360,552 348,546 338,540 330,520 326,500 334,480 332,460 324,440 322,420 328,400 330,380 322,355 320,330 326,305 328,280 322,255 320,230 326,205 328,180 320,155 318,130 324,112 326,95 328,78 Z"/>
      </clipPath>
      <linearGradient id="art-wash" x1="0" y1="0" x2="1" y2="1">
        <stop offset="0" stop-color="#e2e2e2"/>
        <stop offset="0.5" stop-color="#f4f4f4"/>
        <stop offset="1" stop-color="#e0e0e0"/>
      </linearGradient>
    </defs>
    <use href="#paper-shape" fill="#ffffff"/>
    <rect x="310" y="10" width="580" height="560" fill="url(#art-wash)" clip-path="url(#paper-edge)" role="img" aria-label="Faint uncoloured comic background art: city skyline, buildings and action characters"/>
  </svg>

  <h1 class="brand-name">ZING</h1>
  <h2 class="headline">Sign up For a Zing webcomic</h2>
  <p class="tagline">Get free comics like Nova Raiders, Drift Protocol, Ashhorn and more!</p>

  <p class="intro">Start amassing a Zing webcomic and be<br>the envy of your friends and foes alike!</p>

  <form class="signup-form" action="#">
    <input class="email-field" type="email" placeholder="Enter your email" aria-label="Email address">
    <button class="signup-button" type="submit">Sign up</button>
  </form>

  <p class="fine-print">Lorem ipsum dolor sit amet, consectetur adipisicing elit, sed do eius mod tempor incididunt ut labore et dolore magna aliqua. Ut enim ad minim veniam, quis nostrud exercitation ullamco laboris nisi ut</p>

  <div class="blog-badge">
    <svg viewBox="0 0 120 120" width="120" height="120" aria-hidden="true">
      <defs>
        <radialGradient id="badge-fill" cx="0.5" cy="0.45" r="0.6">
          <stop offset="0" stop-color="#fbc226"/>
          <stop offset="1" stop-color="#f2a20c"/>
        </radialGradient>
      </defs>
      <g fill="#ffffff" transform="translate(60 60)">
        <rect x="-44" y="-44" width="88" height="88"/>
        <rect x="-44" y="-44" width="88" height="88" transform="rotate(15)"/>
        <rect x="-44" y="-44" width="88" height="88" transform="rotate(30)"/>
        <rect x="-44" y="-44" width="88" height="88" transform="rotate(45)"/>
        <rect x="-44" y="-44" width="88" height="88" transform="rotate(60)"/>
        <rect x="-44" y="-44" width="88" height="88" transform="rotate(75)"/>
      </g>
      <g fill="url(#badge-fill)" transform="translate(60 60)">
        <rect x="-40" y="-40" width="80" height="80"/>
        <rect x="-40" y="-40" width="80" height="80" transform="rotate(15)"/>
        <rect x="-40" y="-40" width="80" height="80" transform="rotate(30)"/>
        <rect x="-40" y="-40" width="80" height="80" transform="rotate(45)"/>
        <rect x="-40" y="-40" width="80" height="80" transform="rotate(60)"/>
        <rect x="-40" y="-40" width="80" height="80" transform="rotate(75)"/>
      </g>
    </svg>
    <a class="blog-badge-label" href="#"><span class="small">Go to</span><span class="large">Blog</span></a>
  </div>

  <ul class="social-links">
    <li><a href="#" aria-label="Social link 1"></a></li>
    <li><a href="#" aria-label="Social link 2"></a></li>
    <li><a href="#" class="is-active" aria-label="Social link 3"></a></li>
    <li><a href="#" aria-label="Social link 4"></a></li>
    <li><a href="#" aria-label="Social link 5"></a></li>
    <li><a href="#" aria-label="Social link 6"></a></li>
  </ul>
  <p class="copyright">Copyright © 2014 Zing Webcomic All rights reserved.</p>
</main>
</body>
</html>
```